Tellmora Corporate Stationery

Look for design of all new corporate stationery for an existing insurance broking business that is going through a redesign and move from older partners to younger family members. New Logo is attached. Company is Brisbane based.
Colours in the Logo is Hex #43bed8 and website features a lot of hex #17b8d8. Website front page "A plan to protect you" - headline. "Professional and Individual advice to protect your greatest assets" - tagline.

Stationery required: Business Cards, Letter head, Thank-you cards, Birthday cards, Presentation folders, With Compliment slips and a powerpoint template. We also would like to send a card to all customers with the something along of the lines of "something new".

Target Market(s)

Customers of Insurance business looking at superannuation, life and income protection insurance, investment advice and wills

Industry/Entity Type

Insurance Broker

Font styles to use
Other font styles liked:
• same as logo

Requirements
Must have
• The above designs for new stationery for the new business including:
• Business Cards, Letter head, Thank-you cards, Birthday cards, Presentation folders, With Compliment slips and a powerpoint template. We also would like to send a card to all customers with the something along of the lines of "something new".
Nice to have
• It is a new look - long time family business being passed to next generation - big focus on advice for YOU, individual advice etc..

```html
<!DOCTYPE html>
<html lang="en">
<head>
<meta charset="utf-8">
<title>Tellmora Business Card</title>
<link rel="stylesheet" href="https://fonts.googleapis.com/css2?family=Open+Sans:wght@300;400;600&display=swap">
<style>
  :root {
    --cyan: #3bbbd8;
    --cyan-deep: #17b8d8;
    --grey: #7d7d7f;
    --grey-light: #a9a9ab;
    --ink: #555557;
    --white: #ffffff;
    --stage: #ecebe8;
  }
  * { box-sizing: border-box; margin: 0; padding: 0; }
  html, body { width: 1200px; height: 950px; overflow: hidden; }
  body {
    background: var(--stage);
    font-family: "Open Sans", Arial, sans-serif;
    display: flex;
    flex-direction: column;
    align-items: center;
    justify-content: center;
    gap: 60px;
  }
  .card {
    position: relative;
    width: 700px;
    height: 400px;
    overflow: hidden;
    box-shadow: 0 6px 18px rgba(0,0,0,.15);
  }

  /* Front */
  .card-front { background: var(--white); }
  .brand {
    position: absolute;
    left: 60px;
    top: 70px;
    display: flex;
    align-items: center;
    gap: 18px;
  }
  .brand-dot {
    width: 54px; height: 54px;
    border-radius: 50%;
    background: var(--cyan);
    flex: none;
  }
  .brand-name {
    font-size: 46px;
    font-weight: 400;
    letter-spacing: 4px;
    color: var(--cyan);
    line-height: 1;
    text-transform: uppercase;
  }
  .brand-sub {
    font-size: 20px;
    font-weight: 400;
    letter-spacing: 2.5px;
    color: var(--grey);
    text-transform: uppercase;
    margin-top: 4px;
  }
  .person {
    position: absolute;
    right: 50px;
    top: 70px;
    text-align: right;
    color: var(--ink);
  }
  .person-name {
    font-size: 21px;
    font-weight: 400;
    letter-spacing: 1.5px;
    color: var(--cyan);
    text-transform: uppercase;
  }
  .person-role { font-size: 15px; font-weight: 300; margin-top: 2px; letter-spacing: .5px; }
  .person-address { font-size: 15px; font-weight: 300; margin-top: 8px; line-height: 1.45; }
  .contacts {
    position: absolute;
    left: 60px;
    bottom: 44px;
    list-style: none;
    font-size: 15px;
    font-weight: 300;
    color: var(--ink);
    line-height: 1.55;
  }
  .contacts li { display: flex; align-items: center; gap: 10px; }
  .contacts svg { width: 14px; height: 14px; fill: var(--cyan); flex: none; }
  .web-band {
    position: absolute;
    right: 0;
    bottom: 0;
    width: 380px;
    height: 64px;
  }
  .web-band svg { position: absolute; inset: 0; }
  .web-band-text {
    position: absolute;
    right: 40px;
    bottom: 24px;
    font-size: 15px;
    letter-spacing: 3px;
    color: var(--white);
  }

  /* Back */
  .card-back { background: var(--cyan); }
  .back-brand {
    position: absolute;
    left: 60px;
    bottom: 56px;
  }
  .back-brand .brand-name { color: var(--white); font-size: 44px; }
  .back-brand .brand-sub { color: var(--white); }
  .back-web {
    margin-top: 14px;
    font-size: 15px;
    letter-spacing: 5px;
    color: var(--white);
  }
</style>
</head>
<body>

  <section class="card card-front" aria-label="Business card front">
    <div class="brand">
      <span class="brand-dot"></span>
      <div>
        <div class="brand-name">Tellmora</div>
        <div class="brand-sub">Financial Group</div>
      </div>
    </div>

    <div class="person">
      <div class="person-name">Daniel Reeve</div>
      <div class="person-role">CEO/FOUNDER</div>
      <div class="person-address">214 Harbour Row<br>Brisbane, QLD 4000</div>
    </div>

    <ul class="contacts">
      <li>
        <svg viewBox="0 0 16 16" aria-hidden="true"><path d="M3.5 1.5l2.5 0 1 3.5-1.7 1.3a8 8 0 0 0 4.4 4.4L11 9l3.5 1v2.5c0 1-1 2-2 2A11 11 0 0 1 1.5 3.5c0-1 1-2 2-2z"/></svg>
        07 3120 4856
      </li>
      <li>
        <svg viewBox="0 0 16 16" aria-hidden="true"><path d="M4.5 0.5h7a1 1 0 0 1 1 1v13a1 1 0 0 1-1 1h-7a1 1 0 0 1-1-1v-13a1 1 0 0 1 1-1zm0.8 2v9.5h5.4V2.5zM8 12.8a.9.9 0 1 0 0 1.8.9.9 0 0 0 0-1.8z"/></svg>
        0412 558 207
      </li>
      <li>
        <svg viewBox="0 0 16 16" aria-hidden="true"><path d="M4 1h6l2 2v3H4zM1.5 6.5h13v7h-2.5V11h-8v2.5H1.5zM5 12h6v3H5z"/></svg>
        07 3120 4899
      </li>
      <li>
        <svg viewBox="0 0 16 16" aria-hidden="true"><path d="M1 3h14v10H1zM2.3 4.2v.4L8 8.6l5.7-4v-.4zM2.3 6.1v5.6h11.4V6.1L8 10.1z"/></svg>
        hello@tellmora.au
      </li>
    </ul>

    <div class="web-band">
      <svg viewBox="0 0 380 64" preserveAspectRatio="none" aria-hidden="true">
        <polygon points="30,0 380,0 380,64 0,64" fill="var(--cyan)"/>
        <polygon points="0,64 14,44 380,44 380,64" fill="var(--grey-light)" opacity=".55"/>
      </svg>
      <span class="web-band-text">www.tellmora.au</span>
    </div>
  </section>

  <section class="card card-back" aria-label="Business card back">
    <div class="back-brand">
      <div class="brand-name">Tellmora</div>
      <div class="brand-sub">Financial Group</div>
      <div class="back-web">www.tellmora.au</div>
    </div>
  </section>

</body>
</html>
```